Car transport business

We need a new business card design. Attached is our old card sample. I would just like to adjust the logo colors (blue and red) to be brighter. I changed my name to the brighter red and the word dispatcher to a brighter blue as an example. But you can adjust those colors further. And then perhaps you can use the same colors for the card design but use your imagination.

As a suggestion so the card stands out I would like to add a clip art of car carrier truck. Attached are examples of that as well

```html
<!DOCTYPE html>
<html lang="en">
<head>
<meta charset="utf-8">
<title>Northlane Haul – Business Card</title>
<link href="https://fonts.googleapis.com/css2?family=Montserrat:wght@400;600;700&display=swap" rel="stylesheet">
<style>
  :root {
    --bg: #dcdcdc;
    --paper: #ffffff;
    --brand-red: #bc1e2d;
    --brand-blue: #1f5a8c;
    --ink-light: #ffffff;
  }
  * { margin: 0; padding: 0; box-sizing: border-box; }
  html, body {
    width: 1200px; height: 1200px; overflow: hidden;
    background: var(--bg);
    font-family: "Montserrat", Arial, sans-serif;
  }
  .canvas { position: relative; width: 1200px; height: 1200px; }
  .card {
    position: absolute; left: 207px; width: 786px; height: 449px;
  }
  .card--front { top: 112px; background: var(--paper); }
  .card--back { top: 640px; background: var(--brand-red); }

  .identity {
    position: absolute; right: 440px; top: 190px; text-align: right;
  }
  .identity__name {
    color: var(--brand-red); font-weight: 600; font-size: 42px;
    line-height: 1; letter-spacing: 0.5px;
  }
  .identity__role {
    color: var(--brand-blue); font-weight: 400; font-size: 20px;
    line-height: 1; margin-top: 6px; letter-spacing: 0.5px;
  }
  .divider {
    position: absolute; left: 372px; top: 194px; width: 2px; height: 67px;
    background: var(--brand-red);
  }
  .contact {
    position: absolute; left: 398px; top: 190px; list-style: none;
  }
  .contact__item {
    display: flex; align-items: center; height: 25.5px;
    color: var(--brand-blue); font-size: 19px; font-weight: 400;
  }
  .contact__icon { width: 16px; height: 16px; margin-right: 8px; flex: none; }

  .brand {
    position: absolute; left: 130px; top: 168px;
    display: flex; align-items: flex-start;
  }
  .brand__mark {
    width: 92px; height: 92px; border: 6px solid var(--ink-light);
    border-radius: 50%; margin-right: 22px; margin-top: 0;
  }
  .brand__text { margin-top: 66px; }
  .brand__name {
    color: var(--ink-light); font-weight: 700; font-size: 40px; line-height: 1;
    letter-spacing: 1px;
  }
  .brand__tagline {
    color: var(--ink-light); font-weight: 400; font-size: 13.5px;
    letter-spacing: 3.6px; margin-top: 6px; white-space: nowrap;
  }
</style>
</head>
<body>
<main class="canvas">
  <section class="card card--front">
    <div class="identity">
      <p class="identity__name">DALE MORROW</p>
      <p class="identity__role">DISPATCHER</p>
    </div>
    <div class="divider"></div>
    <ul class="contact">
      <li class="contact__item">
        <svg class="contact__icon" viewBox="0 0 16 16" aria-hidden="true">
          <path d="M4 1.5l2 3-1.3 1.2c.6 1.9 2 3.8 3.8 5.1L9.8 9.5l3 2-1.2 2.6C7 13.6 2.7 8.7 2 3z" fill="none" stroke="var(--brand-red)" stroke-width="1.4" stroke-linejoin="round"/>
        </svg>
        555-014-2387
      </li>
      <li class="contact__item">
        <svg class="contact__icon" viewBox="0 0 16 16" aria-hidden="true">
          <rect x="4" y="1.5" width="8" height="4" fill="var(--brand-red)"/>
          <rect x="1" y="5.5" width="14" height="6" rx="1.5" fill="var(--brand-red)"/>
          <rect x="4" y="9.5" width="8" height="5" fill="var(--paper)" stroke="var(--brand-red)" stroke-width="1.2"/>
        </svg>
        555-014-9920
      </li>
      <li class="contact__item">
        <svg class="contact__icon" viewBox="0 0 16 16" aria-hidden="true">
          <rect x="1.5" y="3.5" width="13" height="9" rx="1" fill="none" stroke="var(--brand-red)" stroke-width="1.4"/>
          <path d="M2 4.2l6 4.5 6-4.5" fill="none" stroke="var(--brand-red)" stroke-width="1.4"/>
        </svg>
        northlanehaul@mail.com
      </li>
    </ul>
  </section>

  <section class="card card--back">
    <div class="brand">
      <div class="brand__mark"></div>
      <div class="brand__text">
        <p class="brand__name">NORTHLANE HAUL</p>
        <p class="brand__tagline">THE AUTO TRANSPORT PROFESSIONALS</p>
      </div>
    </div>
  </section>
</main>
</body>
</html>
```